Web-site design for company trading in chemicals & lubricants

We need a standard 5 page web-site designed for our company based in Dubai, UAE.
The web-site should highlight our capacity to store material as well as distribute the same. The products we sell are basic chemicals - packed in bags as well as drums. Bags are big bags - 25 kgs each as well as drums - 200 litres each. We want to highlight the fact that we huge stocks of this material & can deliver by sea & road,
Please use this site as a ref - http://www.brontex-solvents.co.uk/
Besides this, we need a page dedicated to finished products that we are selling for use in the auto industry - lubricants, motor oils,brake-fluids, greases, coolants etc. This are packed in large drums as well as small cans.
It would be nice if the site could immediately also provide a ref. to our location - Dubai or that we are based in the Middle East.
We will provide our company logo for reference

```html
<!DOCTYPE html>
<html lang="en">
<head>
<meta charset="utf-8">
<title>Corvane – Chemicals &amp; Lubricants</title>
<link rel="stylesheet" href="https://fonts.googleapis.com/css2?family=Ubuntu:wght@400;500;700&family=Arimo:wght@400;700&display=swap">
<style>
  :root {
    --brown: #5a3318;
    --olive: #6c5a0c;
    --ink: #3a2a1a;
    --black: #000;
    --panel-grey: #dcdcdc;
    --footer-dark: #353535;
    --footer-darker: #232323;
    --yellow: #e9c94a;
    --yellow-text: #e9c94a;
    --text: #333;
    --white: #fff;
  }
  * { margin: 0; padding: 0; box-sizing: border-box; }
  html, body { width: 892px; height: 1200px; overflow: hidden; background: var(--white); }
  body { position: relative; font-family: "Ubuntu", sans-serif; color: var(--text); }
  .abs { position: absolute; }

  .header-band { left: 0; top: 0; width: 892px; height: 135px; background: linear-gradient(#d9d9d9, #fff 90%); }
  .brand { left: 48px; top: 80px; font-size: 40px; font-weight: 700; letter-spacing: 3px; color: var(--brown); line-height: 40px; }
  .brand-dot { left: 256px; top: 38px; width: 56px; height: 56px; border-radius: 50%; background: var(--olive); opacity: .85; }
  .follow { left: 638px; top: 39px; font-size: 12px; color: #222; }
  .social { top: 35px; width: 22px; height: 22px; border-radius: 50%; }
  .nav { top: 98px; font-size: 13.5px; color: var(--ink); white-space: nowrap; }

  .welcome { left: 28px; top: 150px; width: 258px; height: 264px; background: var(--brown); border-top-left-radius: 22px; color: var(--white); }
  .panel-title { font-size: 13px; text-transform: uppercase; }
  .welcome .panel-title { position: absolute; left: 21px; top: 20px; }
  .quote { position: absolute; font-family: "Arimo", sans-serif; font-weight: 700; font-size: 34px; line-height: 1; }
  .welcome p { position: absolute; left: 23px; top: 64px; width: 230px; font-size: 12px; line-height: 24px; }

  .hero { left: 291px; top: 150px; width: 572px; height: 264px; border-top-right-radius: 22px; background: linear-gradient(180deg, #3f6fb6 0%, #8fb1da 45%, #e8ecef 60%, #c9ccd0 100%); }

  .finder { left: 28px; top: 419px; width: 258px; height: 109px; background: var(--olive); border-bottom-left-radius: 22px; color: var(--white); }
  .finder .panel-title { position: absolute; left: 12px; top: 8px; }
  .finder-input { position: absolute; left: 13px; top: 38px; width: 163px; height: 32px; background: var(--white); }
  .finder-btn { position: absolute; left: 176px; top: 38px; width: 71px; height: 32px; background: #3a3a3a; border: 1px solid var(--white); color: var(--white); font-size: 14px; text-align: center; line-height: 30px; }

  .feature { left: 291px; top: 419px; width: 572px; height: 109px; background: var(--black); border-bottom-right-radius: 22px; color: var(--white); }
  .feature h2 { position: absolute; left: 15px; top: 8px; font-family: "Arimo", sans-serif; font-weight: 400; font-size: 20px; }
  .feature p { position: absolute; left: 15px; top: 39px; width: 545px; font-size: 12px; line-height: 19px; }
  .pill { position: absolute; left: 429px; top: 75px; width: 105px; height: 25px; border-radius: 13px; background: linear-gradient(#f4f4f4, #cfcfcf); color: #333; font-family: "Arimo", sans-serif; font-size: 13px; text-align: center; line-height: 25px; }

  .products-list { left: 28px; top: 533px; width: 258px; height: 340px; background: var(--panel-grey); border-top-left-radius: 22px; color: #333; }
  .products-list .panel-title { position: absolute; left: 18px; top: 26px; font-size: 13px; }
  .products-list ul { position: absolute; left: 22px; top: 62px; list-style: none; font-size: 12px; }
  .products-list li { height: 25px; display: flex; align-items: center; gap: 11px; }

  .intro-title { left: 307px; top: 539px; font-family: "Arimo", sans-serif; font-size: 16px; color: #222; }
  .intro { left: 308px; top: 567px; width: 545px; font-size: 12px; line-height: 24px; color: #333; }

  .card-title { top: 664px; font-size: 15px; color: var(--ink); }
  .card-img { top: 696px; width: 148px; height: 90px; }
  .card-text { top: 795px; width: 170px; font-size: 12px; line-height: 24px; color: #333; }
  .view { top: 847px; width: 62px; height: 20px; background: var(--yellow); border-radius: 3px; font-size: 12px; text-align: center; line-height: 20px; color: #333; }

  .footer-panel { left: 28px; top: 879px; width: 835px; height: 220px; background: var(--footer-dark); color: var(--white); }
  .divider { top: 879px; width: 1px; height: 220px; background: #5a5a5a; }
  .foot-title { top: 893px; font-size: 12px; text-transform: uppercase; color: var(--white); }
  .news { left: 46px; width: 225px; font-size: 12px; line-height: 16px; color: var(--white); }
  .read-more { font-size: 12px; color: var(--yellow-text); display: flex; align-items: center; gap: 7px; }
  .news-rule { left: 41px; top: 1000px; width: 222px; height: 1px; background: #5a5a5a; }
  .field { left: 332px; width: 159px; background: var(--white); border-radius: 8px 0 8px 0; }
  .field-label { left: 509px; font-family: "Arimo", sans-serif; font-weight: 700; font-size: 12px; color: var(--yellow-text); }
  .form-actions { left: 387px; top: 1078px; font-family: "Arimo", sans-serif; font-weight: 700; font-size: 12px; color: var(--yellow-text); white-space: nowrap; }
  .map { left: 623px; top: 932px; width: 224px; height: 149px; background: linear-gradient(135deg, #e9e4d2, #c9d7e6 55%, #efe6c8); }

  .site-footer { left: 27px; top: 1106px; width: 836px; height: 87px; background: var(--footer-darker); border-radius: 22px 22px 0 0; color: var(--white); text-align: center; font-family: "Arimo", sans-serif; }
  .site-footer nav { position: absolute; left: 0; right: 0; top: 21px; font-size: 12px; }
  .site-footer nav span { margin: 0 9px; }
  .site-footer .copy { position: absolute; left: 0; right: 0; top: 48px; font-size: 12px; }
</style>
</head>
<body>
  <header>
    <div class="abs header-band"></div>
    <div class="abs brand-dot"></div>
    <div class="abs brand">CORVANE</div>
    <div class="abs follow">Follow Us On</div>
    <div class="abs social" style="left:721px;background:#2f6fb0"></div>
    <div class="abs social" style="left:755px;background:#5fb3df"></div>
    <div class="abs social" style="left:790px;background:#2f83c0"></div>
    <div class="abs social" style="left:825px;background:#e98a35"></div>
    <nav>
      <span class="abs nav" style="left:430px">About Us</span>
      <span class="abs nav" style="left:507px">Our Products</span>
      <span class="abs nav" style="left:604px">Logistics</span>
      <span class="abs nav" style="left:676px">Business Fields</span>
      <span class="abs nav" style="left:784px">Contact Us</span>
    </nav>
  </header>

  <section class="abs welcome">
    <div class="panel-title">Welcome</div>
    <span class="quote" style="left:6px;top:48px">“</span>
    <p>Lorem Ipsum is simply dummy text of the printing and typesetting industry. Lorem Ipsum has been the industry's standard dummy text ever since the 1500s, when an unknown printer took a galley of type and scrambled it to make a type specimen book.</p>
    <span class="quote" style="left:68px;top:218px">”</span>
  </section>

  <div class="abs hero" role="img" aria-label="White chemical storage silos under a blue sky"></div>

  <section class="abs finder">
    <div class="panel-title">Product Finder</div>
    <div class="finder-input"></div>
    <div class="finder-btn">Search</div>
  </section>

  <section class="abs feature">
    <h2>Lorem Ipsum</h2>
    <p>Lorem Ipsum is simply dummy text of the printing and typesetting industry. Lorem Ipsum has been the industry's standard dummy text ever since the 1500s,</p>
    <div class="pill">Read More</div>
  </section>

  <aside class="abs products-list">
    <div class="panel-title">List of Products</div>
    <ul>
      <li><svg width="7" height="10" viewBox="0 0 7 10"><path d="M1 1l4 4-4 4" fill="none" stroke="#222" stroke-width="2"/></svg>Lorem Ipsum is</li>
      <li><svg width="7" height="10" viewBox="0 0 7 10"><path d="M1 1l4 4-4 4" fill="none" stroke="#222" stroke-width="2"/></svg>simply dummy text</li>
      <li><svg width="7" height="10" viewBox="0 0 7 10"><path d="M1 1l4 4-4 4" fill="none" stroke="#222" stroke-width="2"/></svg>of the printing and</li>
      <li><svg width="7" height="10" viewBox="0 0 7 10"><path d="M1 1l4 4-4 4" fill="none" stroke="#222" stroke-width="2"/></svg>typesetting industry</li>
      <li><svg width="7" height="10" viewBox="0 0 7 10"><path d="M1 1l4 4-4 4" fill="none" stroke="#222" stroke-width="2"/></svg>Lorem Ipsum has</li>
      <li><svg width="7" height="10" viewBox="0 0 7 10"><path d="M1 1l4 4-4 4" fill="none" stroke="#222" stroke-width="2"/></svg>been the industry's</li>
      <li><svg width="7" height="10" viewBox="0 0 7 10"><path d="M1 1l4 4-4 4" fill="none" stroke="#222" stroke-width="2"/></svg>standard dummy</li>
      <li><svg width="7" height="10" viewBox="0 0 7 10"><path d="M1 1l4 4-4 4" fill="none" stroke="#222" stroke-width="2"/></svg>text ever</li>
      <li><svg width="7" height="10" viewBox="0 0 7 10"><path d="M1 1l4 4-4 4" fill="none" stroke="#222" stroke-width="2"/></svg>since the 1500s,</li>
      <li><svg width="7" height="10" viewBox="0 0 7 10"><path d="M1 1l4 4-4 4" fill="none" stroke="#222" stroke-width="2"/></svg>Lorem Ipsum is</li>
    </ul>
  </aside>

  <main>
    <h1 class="abs intro-title" style="font-weight:400">Lorem Ipsum is simply</h1>
    <p class="abs intro">Lorem Ipsum is simply dummy text of the printing and typesetting industry. Lorem Ipsum has been the industry's standard dummy text ever since the 1500s, when an unknown printer took a galley of type and scrambled it to make a type specimen book.</p>

    <h3 class="abs card-title" style="left:301px;font-weight:400">Lubricants</h3>
    <div class="abs card-img" style="left:303px;background:linear-gradient(135deg,#dfe6dc,#3c6e3a 60%,#263a22)" role="img" aria-label="Oiled green gears"></div>
    <p class="abs card-text" style="left:304px">Lorem Ipsum is simply dummy text of the printing</p>
    <div class="abs view" style="left:392px">View</div>

    <h3 class="abs card-title" style="left:495px;font-weight:400">Motor Oils</h3>
    <div class="abs card-img" style="left:495px;background:linear-gradient(135deg,#9a9a9a,#2a2a2a 55%,#d9a81c)" role="img" aria-label="Motor oil poured through a yellow funnel"></div>
    <p class="abs card-text" style="left:492px">Lorem Ipsum is simply dummy text of the printing</p>
    <div class="abs view" style="left:590px">View</div>

    <h3 class="abs card-title" style="left:687px;font-weight:400">Brake-Fluids</h3>
    <div class="abs card-img" style="left:686px;background:linear-gradient(135deg,#c9a47e,#3a3a3a 55%,#d8d8d0)" role="img" aria-label="Brake fluid reservoir in an engine bay"></div>
    <p class="abs card-text" style="left:686px">Lorem Ipsum is simply dummy text of the printing</p>
    <div class="abs view" style="left:778px">View</div>
  </main>

  <footer>
    <div class="abs footer-panel"></div>
    <div class="abs divider" style="left:303px"></div>
    <div class="abs divider" style="left:607px"></div>

    <div class="abs foot-title" style="left:41px">Latest News</div>
    <p class="abs news" style="top:926px">Lorem Ipsum is simply dummy text of the printing and typesetting industry.</p>
    <div class="abs read-more" style="left:180px;top:971px"><svg width="16" height="16" viewBox="0 0 16 16"><circle cx="8" cy="8" r="8" fill="#e9c94a"/><path d="M6 4.5l4 3.5-4 3.5z" fill="#353535"/></svg>Read More</div>
    <div class="abs news-rule"></div>
    <p class="abs news" style="top:1021px">Lorem Ipsum is simply dummy text of the printing and typesetting industry.</p>
    <div class="abs read-more" style="left:180px;top:1065px"><svg width="16" height="16" viewBox="0 0 16 16"><circle cx="8" cy="8" r="8" fill="#e9c94a"/><path d="M6 4.5l4 3.5-4 3.5z" fill="#353535"/></svg>Read More</div>

    <div class="abs foot-title" style="left:334px">Quick Contact</div>
    <div class="abs field" style="top:922px;height:30px"></div>
    <div class="abs field" style="top:959px;height:30px"></div>
    <div class="abs field" style="top:995px;height:75px"></div>
    <div class="abs field-label" style="top:929px">Email</div>
    <div class="abs field-label" style="top:967px">Tele. No.</div>
    <div class="abs field-label" style="top:998px">Comments</div>
    <div class="abs form-actions">Submit &gt;&gt; Reset&gt;&gt;</div>

    <div class="abs foot-title" style="left:621px">Our Location</div>
    <div class="abs map" role="img" aria-label="Street map showing the company location"></div>

    <div class="abs site-footer">
      <nav><span>About Us</span><span>Our Products</span><span>Logistics</span><span>Business Fields</span><span>Contact Us</span></nav>
      <div class="copy">Copyright © 2011 Corvane</div>
    </div>
  </footer>
</body>
</html>
```